Business Card Design for Flood Rescue 360 - Property Restoration Professionals

I need a business card designed for Flood Rescue 360. We are a full-service property restoration solution. Providing water, fire, smoke & storm restoration as well as mold remediation and full remodel or reconstruction to homes and businesses across Dallas-Fort Worth, TX.
Target Market(s)
home and business owners with insurance covered property damage from water, fire or storm related damage
Industry/Entity Type
property restoration
Contact Information for Business Card
Marcus Pelley General Manager Cell: 214-555-0193 Office: 469-555-0148 email: Marcus@FloodRescue360.example services: Water, Fire, Mold, Reconstruction Tagline: Fast Help When the Water Rises!
Look and feel
Each slider illustrates characteristics of the customer's brand and the style your logo design should communicate.

```html
<!DOCTYPE html>
<html lang="en">
<head>
<meta charset="utf-8">
<title>Flood Rescue 360 – Business Card</title>
<link rel="stylesheet" href="https://fonts.googleapis.com/css2?family=Montserrat:wght@400;500;700;800&display=swap">
<style>
  :root {
    --bg: #151515;
    --card-light: #f4f4f4;
    --card-dark: #262626;
    --brand-blue: #16aee0;
    --ink: #2a2a2a;
    --ink-light: #f2f2f2;
  }
  * { margin: 0; padding: 0; box-sizing: border-box; }
  html, body { width: 1200px; height: 1059px; overflow: hidden; background: var(--bg); }
  body { position: relative; font-family: "Montserrat", sans-serif; }

  .card { position: absolute; border-radius: 22px; overflow: hidden; }
  .card-front { left: 257px; top: 89px; width: 687px; height: 390px; background: var(--card-light); color: var(--ink); }
  .card-back { left: 254px; top: 547px; width: 693px; height: 393px; background: var(--card-dark); color: var(--ink-light); }

  .brand-name { font-family: "Montserrat", sans-serif; font-weight: 800; color: var(--brand-blue); text-transform: uppercase; line-height: 1; letter-spacing: -1px; }
  .card-front .brand-name { position: absolute; left: 30px; top: 36px; font-size: 48px; }

  .name-tab { position: absolute; left: 0; top: 186px; width: 16px; height: 42px; background: var(--brand-blue); border-radius: 0 4px 4px 0; }
  .person-name { position: absolute; left: 31px; top: 180px; font-size: 25px; font-weight: 700; color: var(--brand-blue); letter-spacing: 0.5px; }
  .person-title { position: absolute; left: 31px; top: 210px; font-size: 17px; font-weight: 500; }

  .contact-list { position: absolute; left: 30px; top: 249px; list-style: none; }
  .contact-list li { display: flex; align-items: center; height: 28px; font-size: 17.5px; font-weight: 500; }
  .contact-list svg { width: 14px; height: 14px; margin-right: 7px; fill: var(--brand-blue); }

  .address { position: absolute; right: 29px; top: 311px; text-align: right; font-size: 17.5px; font-weight: 500; line-height: 22px; }

  .card-back .brand-name { position: absolute; left: 0; right: 0; top: 108px; text-align: center; font-size: 60px; }

  .services { position: absolute; left: 0; right: 0; top: 314px; text-align: center; font-size: 18px; font-weight: 500; letter-spacing: 0.3px; }
  .services .dot { color: var(--brand-blue); padding: 0 7px; }
  .tagline { position: absolute; left: 0; right: 0; top: 343px; text-align: center; font-size: 17.5px; font-weight: 500; letter-spacing: 0.3px; }
</style>
</head>
<body>

<section class="card card-front">
  <div class="brand-name">Flood<br>Rescue 360</div>

  <div class="name-tab"></div>
  <div class="person-name">MARCUS PELLEY</div>
  <div class="person-title">General Manager</div>

  <ul class="contact-list">
    <li><svg viewBox="0 0 16 16"><path d="M1 7c0-3 3-4 7-4s7 1 7 4v1h-4V6H5v2H1zM4 9h8l2 5H2z"/></svg>469-555-0148</li>
    <li><svg viewBox="0 0 16 16"><path d="M4 1h8v14H4zM5.5 2.5v9h5v-9zM7 12.5h2v1H7z"/></svg>214-555-0193</li>
    <li><svg viewBox="0 0 16 16"><path d="M1 6l7-5 7 5v9H1zM2.5 7v6.5h11V7L8 11z"/></svg>Marcus@FloodRescue360.example</li>
    <li><svg viewBox="0 0 16 16"><circle cx="8" cy="8" r="7"/><path d="M5 4l3 2-1 3 3 1 1 3" stroke="#f4f4f4" stroke-width="1.3" fill="none"/></svg>www.FloodRescue360.example</li>
  </ul>

  <div class="address">4200 Harbor Lane #210<br>Brookhaven, TX 75099</div>
</section>

<section class="card card-back">
  <div class="brand-name">Flood<br>Rescue 360</div>
  <p class="services">Water<span class="dot">•</span>Fire<span class="dot">•</span>Mold<span class="dot">•</span>Reconstruction</p>
  <p class="tagline">Fast Help When the Water Rises!</p>
</section>

</body>
</html>
```